Halden Bus Card

i own a building in the bronx ny - its called "Halden Court Homes"i want a classy logo / business card - nothing too religuous but it is like a family there - its a large apartment building - colors i like dark red, black, medium shade of gray also reg business card stuff tel # 914-555-0173 address 4738 Larkwell Ave Eastvale NY 10931 Email fijosh@aol.comslogan - " Many doors one home "i can send u a picture of the building for the backside

```html
<!DOCTYPE html>
<html lang="en">
<head>
<meta charset="utf-8">
<title>Halden Court Homes – Business Card</title>
<link rel="stylesheet" href="https://fonts.googleapis.com/css2?family=Open+Sans:wght@400;600;700&display=swap">
<style>
  :root {
    --stage: #8c8c8c;
    --card-white: #ffffff;
    --card-dark: #2b2b2b;
    --card-dark-pattern: #333333;
    --brand-red: #d51f1f;
    --ink: #2a2a2a;
    --rule: #b5b5b5;
    --slogan: #f4f4f4;
  }
  * { box-sizing: border-box; margin: 0; padding: 0; }
  html, body {
    width: 1200px; height: 802px; overflow: hidden;
    background: var(--stage);
    font-family: "Open Sans", Arial, sans-serif;
  }
  .stage { position: relative; width: 1200px; height: 802px; }
  .card {
    position: absolute; top: 274px;
    width: 443px; height: 265px;
    box-shadow: 2px 3px 6px rgba(0,0,0,0.35);
    overflow: hidden;
  }
  .card--front { left: 136px; background: var(--card-white); }
  .card--back { left: 624px; background: var(--card-dark); }

  /* Front */
  .brand__mark {
    position: absolute; left: 96px; top: 118px;
    width: 26px; height: 26px; background: var(--brand-red);
  }
  .brand__name {
    position: absolute; left: 150px; top: 88px;
    color: var(--brand-red); font-weight: 600;
    font-size: 27px; line-height: 27px;
  }
  .divider {
    position: absolute; left: 253px; top: 80px;
    width: 1px; height: 103px; background: var(--rule);
  }
  .contact {
    position: absolute; left: 270px; top: 78px;
    color: var(--ink); font-size: 13px; line-height: 16px;
  }
  .contact__name {
    color: var(--brand-red); font-weight: 600; font-size: 15px;
    line-height: 20px; text-transform: uppercase;
  }
  .contact__title { margin-bottom: 7px; }
  .contact__line { display: flex; align-items: center; gap: 3px; }
  .contact__line svg { width: 9px; height: 9px; flex: none; }
  .contact__address { margin-top: 7px; }

  /* Back */
  .back-pattern {
    position: absolute; inset: 0;
    background: linear-gradient(135deg, var(--card-dark-pattern), var(--card-dark));
  }
  .back-mark {
    position: absolute; left: 348px; top: 82px;
    width: 30px; height: 30px; background: var(--brand-red);
  }
  .slogan {
    position: absolute; left: 0; right: 0; top: 196px;
    text-align: center; color: var(--slogan);
    font-weight: 700; font-size: 19.5px; letter-spacing: 0.6px;
    text-transform: uppercase;
  }
</style>
</head>
<body>
<div class="stage">
  <section class="card card--front">
    <span class="brand__mark"></span>
    <div class="brand__name">Halden<br>Court<br>Homes</div>
    <div class="divider"></div>
    <div class="contact">
      <p class="contact__name">Dorian Velcott</p>
      <p class="contact__title">Managing Director</p>
      <p class="contact__line">
        <svg viewBox="0 0 10 10" aria-hidden="true"><path d="M1 4 Q5 0 9 4 L8 5 L6.5 4 L6.5 3 Q5 2.5 3.5 3 L3.5 4 L2 5 Z M2 6 H8 V9 H2 Z" fill="var(--brand-red)"/></svg>
        914-555-0173
      </p>
      <p class="contact__line">
        <svg viewBox="0 0 10 10" aria-hidden="true"><rect x="0.5" y="2" width="9" height="6.5" fill="var(--brand-red)"/><path d="M0.5 2 L5 5.5 L9.5 2" stroke="#fff" stroke-width="0.9" fill="none"/></svg>
        mavreld@quintmail.com
      </p>
      <p class="contact__address">4738 Larkwell Ave<br>Eastvale NY 10931</p>
    </div>
  </section>

  <section class="card card--back">
    <div class="back-pattern" role="img" aria-label="Faint repeating brand pattern on dark background"></div>
    <span class="back-mark"></span>
    <p class="slogan">Many doors one home</p>
  </section>
</div>
</body>
</html>
```